Tiny Meadow Product Label for Tear-Free Head-to-Toe Wash

Need a bottle label design for a new line of natural products targeting infants and children. Products are Pediatrician-developed and paraben-free, sulfate-free, fragrance-free, and cruelty-free. Design should be clean and have a high-end feel to it. Will need other product labels in Tiny Meadow line designed as well in upcoming projects.

Target Market(s)

Newborn to young elementary age children and their parents

Industry/Entity Type

Cosmetics/Beauty

Font styles to use
Other font styles liked:
• Brand fonts are Jost and Sonorous

Colors

Designer to choose colors to be used in the design.

Requirements
Must have
• Tiny Meadow logo, Pediatrician Developed logo, and a clean high-end feel to it. The label must fit the specialty bottle we will be using (label measurements and diagram will be provided) for the front and back of bottle only (NOT the side labels). It must include our list of ingredients (will provide once designer selected).
Nice to have
• Should stand out on the shelf of other baby products due to it's clean simplicity and high-end feel
Should not have
• too much of a "kiddie" feel to it (targeting the parents not the kids)

```html
<!DOCTYPE html>
<html lang="en">
<head>
<meta charset="utf-8">
<title>Tiny Meadow – Tear-Free Head-to-Toe Wash Label</title>
<link rel="stylesheet" href="https://fonts.googleapis.com/css2?family=Jost:ital,wght@0,400;0,500;0,600;0,700;1,600;1,700&display=swap">
<style>
  :root {
    --page-bg: #f3f2ef;
    --label-bg: #fbf9f6;
    --ink: #222222;
    --gold: #9a7230;
    --band-text: #ffffff;
  }
  * { box-sizing: border-box; margin: 0; padding: 0; }
  html, body {
    width: 1200px; height: 1200px; overflow: hidden;
    background: var(--page-bg);
    font-family: "Jost", Arial, sans-serif;
    color: var(--ink);
  }
  .canvas {
    position: relative; width: 1200px; height: 1200px;
    display: flex; justify-content: center; align-items: center; gap: 60px;
  }
  .label {
    position: relative;
    width: 500px; height: 720px;
    background: var(--label-bg);
    border-radius: 50% 50% 0 0 / 70px 70px 0 0;
    box-shadow: 0 2px 14px rgba(0,0,0,0.06);
    display: flex; flex-direction: column; align-items: center;
  }

  /* Front */
  .brand-mark {
    margin-top: 50px;
    width: 200px; height: 200px;
    border: 5px solid var(--gold);
    border-radius: 50%;
  }
  .brand-name {
    margin-top: 18px;
    font-size: 66px; font-weight: 600; letter-spacing: 1px;
    line-height: 1;
  }
  .brand-tagline {
    margin-top: 18px;
    font-size: 16px; font-weight: 600; letter-spacing: 3.6px;
    color: var(--gold); text-transform: uppercase;
  }
  .product-title {
    margin-top: 44px;
    text-align: center;
    font-size: 40px; font-weight: 700; line-height: 1.15;
  }
  .claim-band {
    margin-top: 16px;
    width: 100%; height: 34px;
    background: var(--gold); color: var(--band-text);
    font-size: 23px; font-weight: 400;
    display: flex; align-items: center; justify-content: center;
  }
  .free-badges {
    margin-top: 30px;
    display: flex; gap: 18px;
  }
  .free-badges .badge {
    width: 66px; height: 66px;
    border: 2px solid var(--gold); border-radius: 50%;
  }
  .net-weight {
    margin-top: 26px;
    font-size: 23px; font-weight: 600;
  }

  /* Back */
  .back-mark {
    margin-top: 60px;
    width: 56px; height: 56px;
    border: 3px solid var(--gold); border-radius: 50%;
  }
  .body-copy {
    width: 366px;
    font-size: 20px; line-height: 1.3;
    text-align: justify; text-align-last: center;
  }
  .intro { margin-top: 22px; }
  .section-head {
    margin-top: 18px;
    font-size: 26px; font-weight: 700; font-style: italic;
    color: var(--gold);
  }
  .section-head + .body-copy { margin-top: 8px; }
  .maker {
    margin-top: 22px;
    width: 380px;
    display: flex; justify-content: space-between; align-items: center;
  }
  .maker-text { font-size: 20px; line-height: 1.3; }
  .maker-text .maker-head {
    font-weight: 700; font-style: italic; color: var(--gold);
  }
  .ped-badge {
    width: 86px; height: 86px;
    border: 2px solid var(--gold); border-radius: 50%;
  }
</style>
</head>
<body>
<main class="canvas">

  <section class="label label-front" aria-label="Front label">
    <div class="brand-mark" aria-hidden="true"></div>
    <h1 class="brand-name">Tiny Meadow</h1>
    <p class="brand-tagline">Naturally, for every baby</p>
    <h2 class="product-title">Tear-Free<br>Head-to-Toe Wash</h2>
    <div class="claim-band">Naturally formulated for delicate skin</div>
    <div class="free-badges">
      <span class="badge" role="img" aria-label="Paraben free badge"></span>
      <span class="badge" role="img" aria-label="Sulfate free badge"></span>
      <span class="badge" role="img" aria-label="Fragrance free badge"></span>
      <span class="badge" role="img" aria-label="Cruelty free badge"></span>
    </div>
    <p class="net-weight">Net wt: 73 mL/2,43 fl.oz</p>
  </section>

  <section class="label label-back" aria-label="Back label">
    <div class="back-mark" aria-hidden="true"></div>
    <p class="body-copy intro">A gentle, all-in-one cleanser made with natural ingredients to protect and nourish baby’s delicate hair and skin. Pediatrician-developed and suitable for daily use from newborn onwards.</p>
    <h3 class="section-head">Directions:</h3>
    <p class="body-copy">Dispense a small amount into hands or washcloth. Gently massage into wet hair and skin. Rinse thoroughly. Avoid contact with eyes.</p>
    <h3 class="section-head">Ingredients:</h3>
    <p class="body-copy">Aqua, Glycerin, Decyl Glucoside, Sodium Lauroyl Lactylate, Coco-Glucoside, Glyceryl Oleate, Xanthan Gum, Sodium Benzoate, Citric Acid. (Full list to be finalized.)</p>
    <div class="maker">
      <p class="maker-text">
        <span class="maker-head">Manufactured for</span><br>
        Tiny Meadow Co.<br>
        tinymeadow.com/Made in USA
      </p>
      <span class="ped-badge" role="img" aria-label="Pediatrician developed badge"></span>
    </div>
  </section>

</main>
</body>
</html>
```